Stationary Set Rebrand for Brennick

We are a Canadian Distribution and Service Company that was established in 1969. Over the past 5 decades we have expanded our business and have warehouses across Canada. We specialize in adhesive tapes, adhesives, films, safety, warehouse, shipping, janitorial and packaging supplies.

We have updated our logo design and would like a new corporate branding identity that includes a new fresh Stationary Set (Business Cards, Letterhead, Letterhead MS Word, Envelope, Presentation Folders, Email Signatures, Notepad Covers, etc.)

Target Market(s)

Industrial Business Sector

Font styles to use
Sans Serif

Colors
0054AA
0677BA
7BADD7
CADEEF
E8F1F8
0094D4
00A9DD
6FCCEA
C7EBF8
E9F6FB
00AB8E
00BBA5
67D7C9
C6EFE9
E9F9F6
EB3D1F
EC4F4E
F09395
F8D3D4
FCEDEE

Requirements
Should not have
• Colors not too light, darker colours preferred

```html
<!DOCTYPE html>
<html lang="en">
<head>
<meta charset="utf-8">
<title>Brennick Stationery Set</title>
<link href="https://fonts.googleapis.com/css2?family=Poppins:wght@400;500;700&family=Open+Sans:wght@400;700&display=swap" rel="stylesheet">
<style>
:root{
  --red:#d71920;
  --ink:#111111;
  --paper:#ffffff;
  --bg:#d9dde0;
  --grey:#c9ccce;
  --text:#1d1d1d;
}
*{margin:0;padding:0;box-sizing:border-box}
html,body{width:1200px;height:684px;overflow:hidden;background:var(--bg)}
body{position:relative;font-family:"Open Sans",sans-serif;color:var(--text)}
.piece{position:absolute;background:var(--paper);overflow:hidden;box-shadow:0 2px 6px rgba(0,0,0,.12)}
.band{position:absolute;left:0;bottom:0;width:100%}
.band svg{display:block;width:100%;height:100%}
.wordmark{position:absolute;font-family:"Poppins",sans-serif;font-weight:700;color:var(--ink);letter-spacing:-.5px;line-height:1;display:flex;align-items:center;gap:.18em;white-space:nowrap}
.wordmark .dot{width:.28em;height:.28em;border-radius:50%;background:var(--red);display:inline-block}
.contact{font-family:"Poppins",sans-serif;line-height:1.45;white-space:nowrap}
.contact .ico{display:inline-block;width:.85em;height:.85em;vertical-align:-.1em;margin-right:.35em}
.person-first{color:var(--red);font-weight:700}
.divider-v{position:absolute;width:1px;background:var(--red)}

/* envelope */
.envelope-front{left:50px;top:53px;width:271px;height:120px}
.envelope-front .wordmark{right:8px;top:9px;font-size:20px}
.envelope-front .return{position:absolute;left:196px;top:73px;font-size:5.3px;line-height:1.35}
.envelope-back{left:50px;top:187px;width:271px;height:119px}
.envelope-back .flap{position:absolute;left:3px;top:0;width:265px;height:40px;background:var(--paper);border-radius:0 0 10px 10px;box-shadow:0 4px 6px rgba(0,0,0,.12)}
.envelope-back .seal{position:absolute;left:126px;top:10px;width:14px;height:14px;border-radius:50%;background:var(--red)}

/* business cards */
.card-front{left:51px;top:317px;width:264px;height:150px;border-radius:10px}
.card-front .wordmark{left:50%;top:54px;transform:translateX(-50%);font-size:36px}
.card-back{left:51px;top:484px;width:264px;height:150px;border-radius:10px}
.card-back .wordmark{left:10px;top:60px;font-size:22px}
.card-back .divider-v{left:132px;top:36px;height:78px}
.card-back .person{position:absolute;left:154px;top:42px;font-family:"Poppins",sans-serif}
.card-back .person-name{font-size:14px;line-height:1}
.card-back .person-role{font-size:7px;font-weight:500;margin-top:2px}
.card-back .contact{position:absolute;left:154px;top:75px;font-size:7.4px}
.card-back .address{position:absolute;left:0;width:100%;top:128px;text-align:center;font-family:"Poppins",sans-serif;font-size:7.2px}

/* letterhead */
.letterhead{left:354px;top:55px;width:317px;height:449px}
.letterhead .wordmark{left:17px;top:24px;font-size:29px}
.letterhead .head-contact{position:absolute;right:16px;top:17px;text-align:right;font-size:7px}
.letterhead .head-contact .gap{height:6px}
.letterhead .rule-ink{position:absolute;left:17px;top:67px;width:181px;height:1px;background:var(--ink)}
.letterhead .rule-red{position:absolute;left:198px;top:66px;width:103px;height:2px;background:var(--red)}
.letterhead .letter{position:absolute;left:17px;top:107px;width:283px;font-size:5.9px;line-height:8.3px}
.letterhead .recipient-name,.letterhead .salute{font-family:"Poppins",sans-serif;font-weight:700;font-size:8px;line-height:1.2}
.letterhead .recipient-name{margin-top:7px}
.letterhead .salute{margin:14px 0 6px}
.letterhead p{text-align:justify;margin-bottom:8px}
.letterhead .signature{width:86px;height:20px;margin-top:14px;background:linear-gradient(90deg,rgba(17,17,17,.18),rgba(17,17,17,.06))}
.letterhead .signer{font-family:"Poppins",sans-serif;font-weight:700;font-size:14px;line-height:1.1;margin-top:2px}

/* email signature */
.email-sig{left:354px;top:526px;width:317px;height:106px}
.email-sig .wordmark{left:25px;top:38px;font-size:25px}
.email-sig .divider-v{left:159px;top:12px;height:80px}
.email-sig .person{position:absolute;left:186px;top:12px;font-family:"Poppins",sans-serif}
.email-sig .person-name{font-size:14px;line-height:1}
.email-sig .person-role{font-size:6.6px;font-weight:500;margin-top:1px}
.email-sig .details{position:absolute;left:186px;top:41px;font-size:6.6px}
.email-sig .social{position:absolute;left:140px;top:91px;display:flex;gap:3px}
.email-sig .social span{width:5px;height:5px;border-radius:50%;background:var(--red)}

/* presentation folder */
.folder-cover{left:696px;top:53px;width:139px;height:270px;background:linear-gradient(135deg,#f2f2f2,#c8cacb)}
.folder-cover .feature{position:absolute;left:18px;top:50px;width:104px;height:104px;border-radius:50%;background:var(--red)}
.folder-cover .wordmark{right:9px;top:230px;font-size:17px}
.folder-inside{left:908px;top:68px;width:262px;height:243px;background:linear-gradient(90deg,#ffffff 0%,#eeeeee 46%,#cfd1d2 50%,#c4c6c7 100%)}
.folder-inside .pocket{position:absolute;right:0;bottom:0;width:131px;height:80px;background:var(--red);border-radius:80px 0 0 0}
.folder-inside .pocket-mark{position:absolute;right:38px;bottom:26px;width:26px;height:26px;border-radius:50%;border:1.5px solid var(--paper)}

/* notepad */
.notepad{left:770px;top:392px;width:330px;height:220px}
.notepad .binding{position:absolute;left:0;top:0;width:100%;height:10px;background:repeating-linear-gradient(90deg,#2a2a2a 0 4px,transparent 4px 12px)}
.notepad .feature{position:absolute;left:128px;top:36px;width:120px;height:120px;border-radius:50%;background:var(--red)}
.notepad .wordmark{right:14px;top:172px;font-size:22px}
</style>
</head>
<body>

<svg width="0" height="0" style="position:absolute" aria-hidden="true">
  <defs>
    <symbol id="band" viewBox="0 0 100 10" preserveAspectRatio="none">
      <polygon points="0,0 48,0 51,10 0,10" fill="#111111"/>
      <polygon points="50,0 100,0 100,10 54,10" fill="#d71920"/>
    </symbol>
    <symbol id="i-phone" viewBox="0 0 10 10"><path d="M2 1l2 2-1 1.2c.6 1.3 1.5 2.2 2.8 2.8L7 6l2 2-1.3 1.3C4.5 9 1 5.5.7 2.3z" fill="#d71920"/></symbol>
    <symbol id="i-mail" viewBox="0 0 10 10"><rect x=".8" y="2" width="8.4" height="6" rx="1" fill="#d71920"/><path d="M1 2.5l4 3 4-3" stroke="#fff" stroke-width=".8" fill="none"/></symbol>
    <symbol id="i-web" viewBox="0 0 10 10"><circle cx="5" cy="5" r="4.2" fill="#d71920"/><path d="M.8 5h8.4M5 .8c-2 2.5-2 5.9 0 8.4M5 .8c2 2.5 2 5.9 0 8.4" stroke="#fff" stroke-width=".6" fill="none"/></symbol>
    <symbol id="i-pin" viewBox="0 0 10 10"><path d="M5 .5a3.3 3.3 0 0 0-3.3 3.3C1.7 6.3 5 9.5 5 9.5s3.3-3.2 3.3-5.7A3.3 3.3 0 0 0 5 .5z" fill="#d71920"/><circle cx="5" cy="3.8" r="1.2" fill="#fff"/></symbol>
  </defs>
</svg>

<!-- envelope front -->
<section class="piece envelope-front">
  <div class="wordmark">Brennick<span class="dot"></span></div>
  <div class="return contact">
    418 Alder Ridge Rd. Suite 300<br>Marlow, TX 75902
    <div style="height:6px"></div>
    <svg class="ico"><use href="#i-phone"/></svg>(555) 204-6183<br>
    <svg class="ico"><use href="#i-mail"/></svg>info@brennicksupply.com<br>
    <svg class="ico"><use href="#i-web"/></svg>www.brennicksupply.com
  </div>
  <div class="band" style="height:6px"><svg><use href="#band"/></svg></div>
</section>

<!-- envelope back -->
<section class="piece envelope-back">
  <div class="flap"><span class="seal" role="img" aria-label="Brand leaf emblem on the envelope flap"></span></div>
</section>

<!-- business card front -->
<section class="piece card-front">
  <div class="wordmark">Brennick<span class="dot"></span></div>
  <div class="band" style="height:9px"><svg><use href="#band"/></svg></div>
</section>

<!-- business card back -->
<section class="piece card-back">
  <div class="wordmark">Brennick<span class="dot"></span></div>
  <div class="divider-v"></div>
  <div class="person">
    <div class="person-name"><span class="person-first">Lena</span> Marsh</div>
    <div class="person-role">Founder &amp; CEO</div>
  </div>
  <div class="contact">
    <svg class="ico"><use href="#i-phone"/></svg>(555) 204-6183<br>
    <svg class="ico"><use href="#i-web"/></svg>info@brennicksupply.com<br>
    <svg class="ico"><use href="#i-mail"/></svg>www.brennicksupply.com
  </div>
  <div class="address">418 Alder Ridge Rd. Suite 300 Marlow, TX 75902</div>
  <div class="band" style="height:9px"><svg><use href="#band"/></svg></div>
</section>

<!-- letterhead -->
<section class="piece letterhead">
  <div class="wordmark">Brennick<span class="dot"></span></div>
  <div class="head-contact contact">
    (555) 204-6183 <svg class="ico"><use href="#i-phone"/></svg><br>
    info@brennicksupply.com <svg class="ico"><use href="#i-web"/></svg><br>
    www.brennicksupply.com <svg class="ico"><use href="#i-mail"/></svg>
    <div class="gap"></div>
    418 Alder Ridge Rd. Suite 300 <svg class="ico"><use href="#i-pin"/></svg><br>
    Marlow, TX 75902&nbsp;&nbsp;&nbsp;&nbsp;
  </div>
  <div class="rule-ink"></div>
  <div class="rule-red"></div>
  <div class="letter">
    <div>August-05-2019</div>
    <div class="recipient-name">Daria Kovel</div>
    <div>Director</div>
    <div style="margin-top:6px">418 Alder Ridge Rd. Suite 300<br>Marlow, TX 75902</div>
    <div class="salute">Daria Kovel</div>
    <p>Lorem ipsum dolor sit amet, consectetuer adipiscing elit, sed diam nonummy nibh euismod tincidunt ut laoreet dolore magna aliquam erat volutpat. Ut wisi enim ad minim veniam, quis nostrud exerci tation ullamcorper suscipit lobortis</p>
    <p>Lorem ipsum dolor sit amet, cons ectetuer adipiscing elit, sed diam nonummy nibh euismod tincidunt ut laoreet dolore magna aliquam erat volutpat. Ut wisi enim ad minim veniam, quis nostrud exerci tation ullamcorper suscipit lobortis nisl ut aliquip ex ea commodo consequat. Lorem ipsum dolor sit amet, consectetuer olutpat. Ut wisi enim ad minim veniam, quis nostrud exerci tation ullamcorper suscipit lobortis nisl ut aliquip ex ea commodo consequat. Duis autem</p>
    <p>vel eum iriure dolor in hendrerit in vulputate velit esse molestie consequat, vel illum dolore eu feugiat nulla facilisis at vero eros et accumsan et iusto odio dignissim qui blandit praesent luptatum zzril delenit augue duis dolore te feugait nulla facilisi. Lorem ipsum dolor sit amet, cons ectetuer adipiscing elit, sed diam nonummy nibh euismod tincidunt ut laoreet dolore magna aliquam erat volutpat. Ut wisi enim .</p>
    <div class="signature" role="img" aria-label="Handwritten signature"></div>
    <div class="signer">Evan Hart</div>
    <div>Co-Founder</div>
  </div>
  <div class="band" style="height:12px"><svg><use href="#band"/></svg></div>
</section>

<!-- email signature -->
<section class="piece email-sig">
  <div class="wordmark">Brennick<span class="dot"></span></div>
  <div class="divider-v"></div>
  <div class="person">
    <div class="person-name"><span class="person-first">Lena</span> Marsh</div>
    <div class="person-role">Founder &amp; CEO</div>
  </div>
  <div class="details contact">
    418 Alder Ridge Rd. Suite 300<br>Marlow, TX 75902
    <div style="height:4px"></div>
    <svg class="ico"><use href="#i-phone"/></svg>(555) 204-6183<br>
    <svg class="ico"><use href="#i-web"/></svg>info@brennicksupply.com<br>
    <svg class="ico"><use href="#i-mail"/></svg>www.brennicksupply.com
  </div>
  <div class="social" aria-label="Social links"><span></span><span></span><span></span><span></span><span></span></div>
  <div class="band" style="height:6px"><svg><use href="#band"/></svg></div>
</section>

<!-- presentation folder cover -->
<section class="piece folder-cover">
  <div class="feature" role="img" aria-label="Large brand leaf emblem"></div>
  <div class="wordmark">Brennick<span class="dot"></span></div>
  <div class="band" style="height:8px"><svg><use href="#band"/></svg></div>
</section>

<!-- presentation folder inside -->
<section class="piece folder-inside">
  <div class="pocket"></div>
  <div class="pocket-mark" role="img" aria-label="Outlined brand leaf emblem on pocket"></div>
</section>

<!-- notepad cover -->
<section class="piece notepad">
  <div class="binding"></div>
  <div class="feature" role="img" aria-label="Large brand leaf emblem"></div>
  <div class="wordmark">Brennick<span class="dot"></span></div>
  <div class="band" style="height:9px"><svg><use href="#band"/></svg></div>
</section>

</body>
</html>
```